Solvaquinta Unique Gift Certificate

We need a unique, luxury gift certificate created for our online company (Solvaquinta). We are looking for something out of the ordinary, ie. do not want it to look like a 'normal' gift certificate. Please visit our website to gain a feel for our company (solvaquinta.com.au). The dimensions are 148x148mm. We need our logo, website details, to, from, description, code, exp date included. The certificate will be printed on wood veneer so watermarks will not work. We want it to be clean and minimalistic.

Industry/Entity Type

It Company

```html
<!DOCTYPE html>
<html lang="en">
<head>
<meta charset="utf-8">
<title>Solvaquinta Gift Certificate</title>
<link rel="stylesheet" href="https://fonts.googleapis.com/css2?family=Parisienne&family=Arimo:wght@400&display=swap">
<style>
  :root {
    --teal: #3d9fc2;
    --teal-light: #8fcbe0;
    --teal-pale: #d3edf6;
    --label-grey: #8a8a8a;
    --rule-grey: #5a5a5a;
    --ink: #111111;
    --paper: #ffffff;
  }
  * { margin: 0; padding: 0; box-sizing: border-box; }
  html, body {
    width: 1200px;
    height: 1200px;
    overflow: hidden;
    background: var(--paper);
  }
  .certificate {
    position: relative;
    width: 1200px;
    height: 1200px;
    background: var(--paper);
  }
  .frame {
    position: absolute;
    inset: 0;
  }
  .ornament {
    position: absolute;
    inset: 0;
  }
  .brand-mark {
    position: absolute;
    display: flex;
    align-items: center;
    justify-content: center;
    border: 6px solid var(--teal);
    border-radius: 50%;
    color: var(--teal);
    font-family: "Arimo", Arial, sans-serif;
    font-weight: 400;
  }
  .brand-mark--corner {
    left: 41px;
    top: 120px;
    width: 136px;
    height: 136px;
    font-size: 19px;
  }
  .brand-mark--center {
    left: 520px;
    top: 787px;
    width: 152px;
    height: 152px;
  }
  .brand-name {
    position: absolute;
    left: 0;
    width: 1200px;
    top: 950px;
    text-align: center;
    font-family: "Arimo", Arial, sans-serif;
    font-size: 24px;
    color: var(--teal);
  }
  .title {
    position: absolute;
    left: 0;
    width: 1200px;
    top: 148px;
    text-align: center;
    font-family: "Parisienne", cursive;
    font-size: 70px;
    font-weight: 400;
    color: var(--teal);
    line-height: 1;
  }
  .fields {
    position: absolute;
    left: 202px;
    width: 803px;
    top: 0;
  }
  .field {
    position: absolute;
    left: 0;
    width: 100%;
    display: flex;
    align-items: flex-end;
    height: 40px;
    font-family: "Parisienne", cursive;
    font-size: 29px;
    color: var(--label-grey);
    line-height: 1;
  }
  .field--to { top: 325px; }
  .field--from { top: 434px; }
  .field--description { top: 544px; }
  .field--code { top: 653px; }
  .field__label { padding-right: 8px; white-space: nowrap; }
  .field__rule {
    flex: 1;
    border-bottom: 1.5px solid var(--rule-grey);
    margin-bottom: 4px;
  }
  .field__rule--code { flex: 0 0 313px; margin-right: 17px; }
  .field__label--exp { padding-right: 6px; }
  .date-part {
    border-bottom: 1.5px solid var(--rule-grey);
    margin-bottom: 4px;
  }
  .date-part--day, .date-part--month { width: 64px; }
  .date-part--year { flex: 1; }
  .date-sep {
    font-family: "Arimo", Arial, sans-serif;
    font-size: 30px;
    color: var(--rule-grey);
    padding: 0 2px;
  }
  .website {
    position: absolute;
    left: 0;
    width: 1200px;
    top: 1022px;
    text-align: center;
    font-family: "Arimo", Arial, sans-serif;
    font-size: 26px;
    color: var(--ink);
  }
</style>
</head>
<body>
<main class="certificate">

  <svg class="ornament" width="1200" height="1200" viewBox="0 0 1200 1200">
    <defs>
      <linearGradient id="flourish-tone" x1="0" y1="0" x2="1" y2="1">
        <stop offset="0" stop-color="var(--teal-pale)"/>
        <stop offset="1" stop-color="var(--teal-light)"/>
      </linearGradient>
    </defs>
    <g role="img" aria-label="Teal interlaced knot flourish at the top right corner">
      <path d="M757 84 H1118 V409 H1066 V132 H757 Z" fill="url(#flourish-tone)" opacity="0.55"/>
    </g>
    <g role="img" aria-label="Teal interlaced knot flourish at the bottom left corner">
      <path d="M75 777 H127 V1066 H437 V1118 H75 Z" fill="url(#flourish-tone)" opacity="0.55"/>
    </g>
    <g role="img" aria-label="Teal interlaced knot flourish at the bottom right corner">
      <path d="M1066 777 H1118 V1118 H757 V1066 H1066 Z" fill="url(#flourish-tone)" opacity="0.55"/>
    </g>
    <g role="img" aria-label="Small teal scroll ornament left of the title">
      <rect x="262" y="172" width="109" height="44" rx="22" fill="url(#flourish-tone)" opacity="0.6"/>
    </g>
    <g role="img" aria-label="Small teal scroll ornament right of the title">
      <rect x="846" y="172" width="112" height="44" rx="22" fill="url(#flourish-tone)" opacity="0.6"/>
    </g>
  </svg>

  <svg class="frame" width="1200" height="1200" viewBox="0 0 1200 1200" aria-hidden="true">
    <g stroke="var(--teal)" stroke-width="2" fill="none">
      <line x1="207" y1="97" x2="1078" y2="97"/>
      <line x1="207" y1="103" x2="1078" y2="103"/>
      <line x1="1088" y1="97" x2="1088" y2="1090"/>
      <line x1="1094" y1="97" x2="1094" y2="1090"/>
      <line x1="97" y1="311" x2="97" y2="1090"/>
      <line x1="103" y1="311" x2="103" y2="1090"/>
      <line x1="97" y1="1087" x2="1094" y2="1087"/>
      <line x1="97" y1="1093" x2="1094" y2="1093"/>
    </g>
    <circle cx="207" cy="99" r="6" fill="var(--teal)"/>
    <circle cx="99" cy="311" r="6" fill="var(--teal)"/>
  </svg>

  <div class="brand-mark brand-mark--corner">Solvaquinta</div>

  <h1 class="title">Gift Certificate</h1>

  <section class="fields">
    <div class="field field--to">
      <span class="field__label">To:</span>
      <span class="field__rule"></span>
    </div>
    <div class="field field--from">
      <span class="field__label">From:</span>
      <span class="field__rule"></span>
    </div>
    <div class="field field--description">
      <span class="field__label">Description:</span>
      <span class="field__rule"></span>
    </div>
    <div class="field field--code">
      <span class="field__label">Code:</span>
      <span class="field__rule field__rule--code"></span>
      <span class="field__label field__label--exp">Exp Date:</span>
      <span class="date-part date-part--day"></span>
      <span class="date-sep">/</span>
      <span class="date-part date-part--month"></span>
      <span class="date-sep">/</span>
      <span class="date-part date-part--year"></span>
    </div>
  </section>

  <div class="brand-mark brand-mark--center" aria-hidden="true"></div>
  <p class="brand-name">solvaquinta</p>

  <p class="website">www.solvaquinta.com.au</p>

</main>
</body>
</html>
```